Harborline Auto LLC

Car Dealer Customer Service
Address: 2874 Cresthaven Road, Shelbyville, TN 37162
web: www.harborlineautoxq.net
email: harborlineautoxq@mailnest.example
Phone: (931) 555-0148
Phone: (629) 555-0173

```html
<!DOCTYPE html>
<html lang="en">
<head>
<meta charset="utf-8">
<title>Harborline Auto – Business Card</title>
<link rel="stylesheet" href="https://fonts.googleapis.com/css2?family=Montserrat:wght@800&family=Mulish:wght@500;600&display=swap">
<style>
  :root {
    --backdrop: #323232;
    --brand-blue: #1e7bac;
    --wave-blue: #2a93d0;
    --name-blue: #1b72a6;
    --accent-gold: #efb440;
    --ink: #1d1d1d;
    --paper: #ffffff;
  }
  * { margin: 0; padding: 0; box-sizing: border-box; }
  html, body {
    width: 1200px; height: 984px; overflow: hidden;
    background: var(--backdrop);
  }
  .stage { position: relative; width: 1200px; height: 984px; }
  .card {
    position: absolute; left: 250px; width: 700px; height: 400px;
    overflow: hidden;
    box-shadow: 0 8px 24px rgba(0,0,0,.45);
  }
  .card-front { top: 62px; background: var(--brand-blue); }
  .card-back { top: 522px; background: var(--paper); }

  .brand-mark { position: absolute; border-radius: 50%; }
  .brand-name {
    position: absolute; font-family: "Montserrat", sans-serif;
    font-weight: 800; letter-spacing: 1px; white-space: nowrap;
  }
  .card-front .brand-mark {
    left: 300px; top: 80px; width: 100px; height: 100px;
    background: var(--paper);
  }
  .card-front .brand-name {
    left: 0; right: 0; top: 210px; text-align: center;
    font-size: 46px; color: var(--paper);
  }

  .card-back .wave { position: absolute; inset: 0; }
  .card-back .brand-mark {
    left: 130px; top: 70px; width: 90px; height: 90px;
    background: var(--wave-blue);
  }
  .card-back .brand-name {
    left: 16px; width: 318px; top: 178px; text-align: center;
    font-size: 25px; letter-spacing: 0.5px; color: var(--name-blue);
  }
  .divider {
    position: absolute; left: 352px; top: 58px; width: 2px; height: 190px;
    background: var(--wave-blue);
  }
  .contact {
    position: absolute; left: 370px; top: 58px;
    font-family: "Mulish", sans-serif; font-weight: 600;
    color: var(--ink); font-size: 15px; line-height: 1.3;
  }
  .contact .role { margin-left: 24px; margin-bottom: 8px; }
  .contact .address { margin-left: 24px; margin-bottom: 8px; }
  .contact .line { display: flex; align-items: center; gap: 8px; margin-bottom: 4px; }
  .contact .icon { width: 16px; height: 16px; flex: none; }
  .contact .domain { color: var(--wave-blue); }
</style>
</head>
<body>
<div class="stage">
  <section class="card card-front">
    <span class="brand-mark"></span>
    <p class="brand-name">HARBORLINE AUTO</p>
  </section>

  <section class="card card-back">
    <svg class="wave" viewBox="0 0 700 400" width="700" height="400" aria-hidden="true">
      <path d="M0,225 C60,330 200,345 380,345 C520,345 620,360 700,392 L700,400 L0,400 Z" fill="var(--wave-blue)"/>
      <path d="M60,285 C150,338 300,326 420,328 C540,330 620,352 680,384" fill="none" stroke="var(--accent-gold)" stroke-width="4" stroke-linecap="round"/>
    </svg>
    <span class="brand-mark"></span>
    <p class="brand-name">HARBORLINE AUTO</p>
    <span class="divider"></span>
    <div class="contact">
      <p class="role">Car Dealer Customer Service</p>
      <p class="address">2874 Cresthaven Road,<br>Shelbyville, TN 37162</p>
      <p class="line">
        <svg class="icon" viewBox="0 0 16 16"><path d="M4 1l3 3-2 2c1 2 3 4 5 5l2-2 3 3-2 2C7 14 2 9 2 3z" fill="var(--wave-blue)"/></svg>
        (931) 555-0148
      </p>
      <p class="line">
        <svg class="icon" viewBox="0 0 16 16"><path d="M1 6c0-2 14-2 14 0v1h-3V6H4v1H1z M3 8h10l1 6H2z" fill="var(--wave-blue)"/></svg>
        (629) 555-0173
      </p>
      <p class="line">
        <svg class="icon" viewBox="0 0 16 16"><rect x="1" y="3" width="14" height="10" fill="var(--wave-blue)"/><path d="M1 3l7 6 7-6" fill="none" stroke="#fff" stroke-width="1.3"/></svg>
        harborlineautoxq@mailnest.example
      </p>
      <p class="line">
        <svg class="icon" viewBox="0 0 16 16"><circle cx="8" cy="8" r="7" fill="var(--wave-blue)"/><path d="M1 8h14M8 1c-3 3-3 11 0 14M8 1c3 3 3 11 0 14" fill="none" stroke="#fff" stroke-width="1"/></svg>
        <span>www.<span class="domain">harborlineautoxq</span>.net</span>
      </p>
    </div>
  </section>
</div>
</body>
</html>
```